Need help in designing new business card utilizing our new logo.

BuildMark Solutions works with Construction Business Owners, Managers & IT Professionals to strengthen software usage and increase user productivity.

Our Construction Accounting and Mobile Field Management Software Clients engage with us in the following areas:

New Software Implementations
Software Re-Implementations
Redesigning Software Usage at the User Level
Project Coordination & Management
Continued Software Support

Old tag line:
Weighing Options - Implementing Solutions

www.buildmark-solutions.example

Ridge 4 is a product, but not needed for a new business card.

```html
<!DOCTYPE html>
<html lang="en">
<head>
<meta charset="utf-8">
<title>BuildMark Solutions – Business Card</title>
<link rel="stylesheet" href="https://fonts.googleapis.com/css2?family=Montserrat:wght@400;500;600;700&family=Arimo:wght@400&display=swap">
<style>
  :root {
    --brand-blue: #2e3590;
    --brand-blue-mid: #5a5fa6;
    --brand-grey: #b9bbc4;
    --card-grey-top: #b4b5c0;
    --white: #ffffff;
    --page-bg: #e9e8e4;
    --text-light: #ffffff;
  }
  * { box-sizing: border-box; margin: 0; padding: 0; }
  html, body { width: 900px; height: 1200px; overflow: hidden; }
  body { background: var(--page-bg); position: relative; font-family: "Arimo", Arial, sans-serif; }

  .card {
    position: absolute;
    left: 88px;
    width: 734px;
    height: 430px;
    border-radius: 22px;
    overflow: hidden;
    box-shadow: 0 6px 14px rgba(0,0,0,0.25);
  }

  /* Front */
  .card-front {
    top: 125px;
    background: linear-gradient(180deg, var(--card-grey-top) 0%, var(--brand-blue-mid) 30%, var(--brand-blue) 58%, var(--brand-blue) 100%);
    color: var(--text-light);
  }
  .company-name {
    position: absolute; left: 48px; top: 58px;
    font-family: "Montserrat", sans-serif; font-weight: 600;
    font-size: 36px; letter-spacing: 1px; text-transform: uppercase;
    color: var(--white);
  }
  .person-name {
    position: absolute; left: 48px; top: 180px;
    font-family: "Montserrat", sans-serif; font-weight: 700; font-size: 19px; letter-spacing: 0.5px;
  }
  .person-title {
    position: absolute; left: 48px; top: 204px;
    font-family: "Montserrat", sans-serif; font-weight: 600; font-size: 13px; letter-spacing: 0.5px;
  }
  .address {
    position: absolute; left: 48px; top: 236px;
    font-size: 16px; line-height: 23px;
  }
  .contact-list { position: absolute; left: 48px; top: 294px; list-style: none; font-size: 16px; }
  .contact-list li { display: flex; align-items: center; height: 23.5px; }
  .contact-list svg { width: 13px; height: 13px; margin-right: 10px; fill: var(--white); }
  .front-rule {
    position: absolute; left: 48px; right: 52px; top: 375px;
    border-top: 1.5px solid rgba(255,255,255,0.85);
  }
  .front-tagline {
    position: absolute; left: 48px; top: 387px;
    font-family: "Montserrat", sans-serif; font-weight: 500; font-size: 19.5px; letter-spacing: 0.6px;
  }

  /* Back */
  .card-back { top: 640px; background: var(--white); }
  .brand-lockup {
    position: absolute; left: 0; right: 0; top: 150px;
    display: flex; align-items: center; justify-content: center; gap: 22px;
  }
  .brand-square { width: 58px; height: 58px; background: var(--brand-blue); }
  .brand-name {
    font-family: "Montserrat", sans-serif; font-weight: 700;
    font-size: 44px; color: var(--brand-blue);
  }
  .web-address {
    position: absolute; left: 0; right: 0; top: 353px; text-align: center;
    font-family: "Montserrat", sans-serif; font-weight: 600; font-size: 16px;
    letter-spacing: 8px; color: var(--brand-blue); text-transform: uppercase;
  }
  .tagline-band {
    position: absolute; left: 0; right: 0; bottom: 0; height: 42px;
    background: var(--brand-blue);
  }
  .tagline-wedge {
    position: absolute; left: 0; bottom: 0; width: 100px; height: 42px;
    background: var(--brand-grey);
    clip-path: polygon(0 0, 40% 0, 100% 100%, 0 100%);
  }
  .tagline {
    position: absolute; left: 82px; bottom: 0; height: 42px; line-height: 44px;
    font-family: "Montserrat", sans-serif; font-weight: 400; font-size: 20.5px;
    color: var(--white); text-transform: uppercase;
  }
  .tagline strong { font-weight: 700; }
</style>
</head>
<body>

<section class="card card-front">
  <div class="company-name">BuildMark Solutions</div>
  <div class="person-name">DANA R. WHITLOW</div>
  <div class="person-title">OWNER</div>
  <div class="address">14B Harlow Street- PMB 118<br>Millbrook NY 12545</div>
  <ul class="contact-list">
    <li><svg viewBox="0 0 24 24" aria-hidden="true"><path d="M6.6 10.8a15.1 15.1 0 0 0 6.6 6.6l2.2-2.2a1 1 0 0 1 1-.25 11.4 11.4 0 0 0 3.6.57 1 1 0 0 1 1 1V20a1 1 0 0 1-1 1A17 17 0 0 1 3 4a1 1 0 0 1 1-1h3.5a1 1 0 0 1 1 1c0 1.25.2 2.45.57 3.57a1 1 0 0 1-.25 1z"/></svg>866-555-0142 ext.100</li>
    <li><svg viewBox="0 0 24 24" aria-hidden="true"><path d="M7 1h10a2 2 0 0 1 2 2v18a2 2 0 0 1-2 2H7a2 2 0 0 1-2-2V3a2 2 0 0 1 2-2zm0 3v14h10V4zm5 15.5a1 1 0 1 0 0 2 1 1 0 0 0 0-2z"/></svg>518-555-0187</li>
    <li><svg viewBox="0 0 24 24" aria-hidden="true"><path d="M2 5h20v14H2zm2 2v.5l8 5 8-5V7zm0 2.8V17h16V9.8l-8 5z"/></svg>dana.whitlow@buildmark-solutions.example</li>
  </ul>
  <div class="front-rule"></div>
  <div class="front-tagline">CONSTRUCTION ACCOUNTING SOFTWARE CONSULTANTS</div>
</section>

<section class="card card-back">
  <div class="brand-lockup">
    <div class="brand-square"></div>
    <div class="brand-name">BuildMark Solutions</div>
  </div>
  <div class="web-address">www.buildmark-solutions.example</div>
  <div class="tagline-band"></div>
  <div class="tagline-wedge"></div>
  <div class="tagline"><strong>Weighing</strong> Options – <strong>Implementing</strong> Solutions</div>
</section>

</body>
</html>
```